Business card design needed

Family General Practitioner/ Family Physician.
Logo is the logo of the Noble Guild of Family Healers Oceania
http://kpltw.varendo.example/ImageShelf/marks/pages/NGFHO%20mark_jpg.htm
Updates

Project Deadline Extended
Reason: Just a bit more time to make changes and the weekend for me to look at things closely and to choose. Thanks, Orin

Thanks for all the submissions. So many of them are really works of art. Not one of them are not good. The ones that I am eliminating are the ones that I think are not suitable for me personally only, and because if I don't, it makes it very difficult to decide as many of you are also sending me slight variations of a card. I have just decided to choose a second place card too. Can't thank you all enough. Good luck, Orin. P.S - Working today till 10 pm as the card says :-), so probably won't be able to give a feedback till late Saturday night or Sunday morning here in Sydney, Australia. 

Project Deadline Extended
Reason: Just added a second place to the budget and realised that Australia is ahead of the rest of the world in the time zone (only :-) - don't want to offend anyone or start a debate!! ) , so Monday deadline will mean it will be a weekend for the rest of the world. Just wanted to give everyone more time to submit their best, especially since I will be picking a second card too. Can't thank everyone enough for the submissions. P.S - Not keen on photos on the card.

Industry/Entity Type

Business

Contact Information for Business Card

Dr. Orin Halvey M.B.B.S., F.N.G.F.H.O
Family General Practitioner
Address, timings, phone and fax number on the back.

Requirements
Must have
• Timings
Mon 7 am - 7 pm
Tues 7 am - 12 pm
Wed 7 am - 10 pm
Thurs 7 am - 12 pm
Fri 7 am - 8 pm
Sat 8 am - 10 pm
Sun - Off

```html
<!DOCTYPE html>
<html lang="en">
<head>
<meta charset="utf-8">
<title>Dr. Orin Halvey – Business Card</title>
<link rel="stylesheet" href="https://fonts.googleapis.com/css2?family=Pinyon+Script&family=Crimson+Text:ital@0;1&display=swap">
<style>
  :root {
    --page-bg: #ffffff;
    --card-centre: #30699a;
    --card-mid: #254e92;
    --card-edge: #3c4682;
    --ink-light: #ffffff;
    --mark-ring: rgba(255, 255, 255, 0.85);
  }
  * { margin: 0; padding: 0; box-sizing: border-box; }
  html, body {
    width: 1200px;
    height: 741px;
    overflow: hidden;
    background: var(--page-bg);
  }
  .business-card {
    position: absolute;
    left: 32px;
    top: 54px;
    width: 1135px;
    height: 646px;
    background: radial-gradient(ellipse 62% 72% at 49% 38%, var(--card-centre) 0%, var(--card-mid) 62%, var(--card-edge) 100%);
    color: var(--ink-light);
    font-family: "Crimson Text", Georgia, serif;
  }
  .guild-mark {
    position: absolute;
    left: 822px;
    top: 40px;
    width: 300px;
    display: flex;
    flex-direction: column;
    align-items: center;
    gap: 14px;
  }
  .guild-mark__disc {
    width: 110px;
    height: 110px;
    border-radius: 50%;
    border: 3px solid var(--mark-ring);
  }
  .guild-mark__name {
    font-size: 24px;
    line-height: 1.2;
    text-align: center;
    color: var(--ink-light);
  }
  .tagline {
    position: absolute;
    right: 16px;
    top: 296px;
    font-size: 33px;
    font-style: italic;
    letter-spacing: 0.3px;
  }
  .practitioner-name {
    position: absolute;
    left: 58px;
    top: 360px;
    font-family: "Pinyon Script", cursive;
    font-size: 72px;
    font-weight: 400;
    line-height: 1;
  }
  .qualifications {
    position: absolute;
    left: 60px;
    top: 496px;
    font-size: 31px;
    letter-spacing: 0.5px;
  }
  .role {
    position: absolute;
    left: 60px;
    top: 548px;
    font-size: 38px;
  }
</style>
</head>
<body>
  <main class="business-card">
    <div class="guild-mark">
      <div class="guild-mark__disc"></div>
      <p class="guild-mark__name">Noble Guild of Family Healers Oceania</p>
    </div>
    <p class="tagline">Caring for your health</p>
    <h1 class="practitioner-name">Dr. Orin Halvey</h1>
    <p class="qualifications">M.B.B.S., F.N.G.F.H.O</p>
    <p class="role">Family General Practitioner</p>
  </main>
</body>
</html>
```